Square graphic for social media post

I want to create a 1080 x 1080px all-black image for the quote below that I can share on social media. I want the emphasis to be primarily on the quote, secondarily on the portrait, and third (smallest) on the logo. I want the background on the portrait to be edited so it's transparent and just shows the face of the person on a black background (no brick wall visible).

Graphic color: black
Text color: white
Content: "What we went through is going to make the greatest generation of hoteliers our industry has ever seen." << biggest text
Derek Holm << smaller text
President, Silverbrook Hotels << smaller text
[image of person - use whichever version looks better to you]
[Add Lodging Ledger logo - whichever looks better to you]

This image needs to be readable when sized down much smaller (400x400?) so want the text and portrait to take up most of the space.

I'd like the output both as PNG and original file (preferably Canva). Thanks!

Target Market(s)

Hotel managers

Industry/Entity Type

Hospitality

Font styles to use
Sans Serif

Colors

Designer to choose colors to be used in the design.

Requirements
Must have
• Needs to focus on the quote and the person quoted (the portrait)

```html
<!DOCTYPE html>
<html lang="en">
<head>
<meta charset="utf-8">
<title>Lodging Ledger – Quote Card</title>
<link rel="stylesheet" href="https://fonts.googleapis.com/css2?family=Arimo:wght@400;700&display=swap">
<style>
  :root {
    --bg: #000000;
    --ink: #ffffff;
    --frame: #e9e9e9;
    --caption: #e4e4e4;
    --portrait-light: #d9d9d9;
    --portrait-dark: #6f6f6f;
  }
  * { margin: 0; padding: 0; box-sizing: border-box; }
  html, body {
    width: 1200px;
    height: 1200px;
    overflow: hidden;
    background: var(--bg);
  }
  .quote-card {
    position: relative;
    width: 1200px;
    height: 1200px;
    background: var(--bg);
    font-family: "Arimo", Arial, sans-serif;
    color: var(--ink);
  }
  .brand-name {
    position: absolute;
    top: 142px;
    left: 0;
    width: 1200px;
    text-align: center;
    font-size: 38px;
    font-weight: 700;
    letter-spacing: 8px;
    line-height: 1;
    color: var(--ink);
  }
  .quote-frame {
    position: absolute;
    left: 0;
    top: 0;
    width: 1200px;
    height: 1200px;
  }
  .quote-line {
    position: absolute;
    left: 194px;
    line-height: 1;
    white-space: nowrap;
    font-weight: 400;
  }
  .quote-line--lead { font-size: 73px; }
  .quote-line--one { top: 396px; }
  .quote-line--two { top: 482px; }
  .quote-line--three { top: 571px; font-size: 51px; }
  .quote-line--four { top: 629px; font-size: 60px; }
  .speaker-portrait {
    position: absolute;
    left: 467px;
    top: 806px;
    width: 266px;
    height: 266px;
    border-radius: 50%;
    background: radial-gradient(circle at 50% 45%, var(--portrait-light) 0%, #a9a9a9 55%, var(--portrait-dark) 100%);
  }
  .speaker-name {
    position: absolute;
    top: 1096px;
    left: 0;
    width: 1200px;
    text-align: center;
    font-size: 31px;
    font-weight: 400;
    letter-spacing: 1px;
    line-height: 1;
    color: var(--caption);
  }
  .speaker-role {
    position: absolute;
    top: 1139px;
    left: 0;
    width: 1200px;
    text-align: center;
    font-size: 26px;
    font-weight: 400;
    line-height: 1;
    color: var(--caption);
  }
</style>
</head>
<body>
  <main class="quote-card">
    <div class="brand-name">LODGING LEDGER</div>

    <svg class="quote-frame" viewBox="0 0 1200 1200" aria-hidden="true">
      <g fill="none" stroke="var(--frame)" stroke-width="5.5" stroke-linecap="round">
        <path d="M205 339 H1066 A17 17 0 0 1 1083 356 V656"/>
        <path d="M106 450 V742 A17 17 0 0 0 123 759 H953"/>
      </g>
      <g class="quote-mark quote-mark--open" fill="var(--frame)">
        <path d="M108 340 Q112 333 121 333 L130 333 L124 394 L104 394 Z"/>
        <path d="M142 340 Q146 333 155 333 L164 333 L158 394 L138 394 Z"/>
      </g>
      <g class="quote-mark quote-mark--close" fill="var(--frame)">
        <path d="M1025 689 L1045 689 L1041 743 Q1037 750 1028 750 L1019 750 Z"/>
        <path d="M1059 689 L1079 689 L1075 743 Q1071 750 1062 750 L1053 750 Z"/>
      </g>
    </svg>

    <blockquote class="quote-text">
      <div class="quote-line quote-line--lead quote-line--one">What we went through</div>
      <div class="quote-line quote-line--lead quote-line--two">is going to make the</div>
      <div class="quote-line quote-line--three">greatest generation of hoteliers</div>
      <div class="quote-line quote-line--four">our industry has ever seen</div>
    </blockquote>

    <div class="speaker-portrait" role="img" aria-label="Head-and-shoulders portrait of Derek Holm in a blue blazer on a soft grey background"></div>
    <div class="speaker-name">DEREK HOLM</div>
    <div class="speaker-role">President, Silverbrook Hotels</div>
  </main>
</body>
</html>
```